Website for Life Strategies business

We need a website to present our video, audio and print content to subcribers at Bright Summit Mentors. We will offer a team of coaches who can help people breakthrough the barriers that keep them from reaching their physical, spiritual, financial, leadership and relationship goals.

Target Market(s)

Anyone who needs help with strategies to take their life to a new level of success.

Industry/Entity Type

Life Coaching

Logo Text

Bright Summit Mentors

Number of Pages Required

5+ page

Colors

Designer to choose colors to be used in the design.

Requirements
Must have
• The ability to present content as a package that includes Word Documents, videos and audio content as well as to be able to display books for sale. Each week their would be a new package for subscribers to access. It should provide the ability for subscribers to comment on the material and share how their lives were changed by the content. Should also include a shop page to offer merchandise for sale.
Nice to have
• Not sure
Should not have
• Not sure

```html
<!DOCTYPE html>
<html lang="en">
<head>
<meta charset="utf-8">
<title>Bright Summit Mentors</title>
<link href="https://fonts.googleapis.com/css2?family=Open+Sans:wght@400;600;700&display=swap" rel="stylesheet">
<style>
:root{
  --brand:#0c47a0;
  --brand-dark:#0a3d8a;
  --nav:#1d3c6b;
  --ink:#222;
  --muted:#555;
  --rule:#b5b5b5;
  --soft:#ebebed;
  --white:#fff;
  --accent:#f05a28;
}
*{box-sizing:border-box;margin:0;padding:0}
html,body{width:1200px;height:3364px;overflow:hidden}
body{font-family:"Open Sans",Arial,sans-serif;color:var(--ink);background:var(--white);position:relative}
.abs{position:absolute}
section,header,footer,nav{position:absolute;left:0;width:1200px}

/* header */
.site-header{top:0;height:99px;background:var(--white)}
.brand{left:130px;top:26px;font-size:30px;font-weight:600;color:var(--brand);white-space:nowrap}
.call{left:728px;top:33px;display:flex;align-items:center;gap:10px}
.call-icon{width:30px;height:30px;border-radius:50%;background:var(--brand);display:flex;align-items:center;justify-content:center}
.call-label{font-size:10px;font-weight:700;color:var(--ink)}
.call-number{font-size:16px;color:var(--brand);font-weight:600}
.search{left:962px;top:31px;width:106px;height:34px;border:1px solid #cfcfcf;display:flex;align-items:center;gap:6px;padding-left:10px;font-size:9px;color:#777}

/* nav */
.main-nav{top:99px;height:34px;background:var(--nav)}
.main-nav ul{list-style:none;position:absolute;left:128px;width:940px;height:34px;display:flex;justify-content:space-between}
.main-nav li{font-size:11px;color:var(--white);height:34px;line-height:34px;width:108px;text-align:center;font-weight:600}
.main-nav li.active{background:var(--brand)}

/* hero */
.hero{top:133px;height:527px;background:linear-gradient(180deg,#3f82c8 0%,#8fbde6 38%,#d9e4ee 60%,#c89a8c 82%,#b07466 100%)}
.hero-title{left:130px;top:262px;font-size:46px;font-weight:700;color:var(--white)}
.hero-sub{left:130px;top:330px;font-size:19px;color:var(--white)}
.btn-solid{background:var(--brand);color:var(--white);font-size:13px;font-weight:700;display:flex;align-items:center;justify-content:center;gap:12px}
.hero-btn{left:130px;top:392px;width:158px;height:46px}
.dots{left:546px;top:480px;display:flex;gap:14px}
.dots span{width:9px;height:9px;border-radius:50%;background:rgba(255,255,255,.55)}
.dots span:first-child{background:var(--white)}

/* section titles */
.section-title{width:1200px;left:0;text-align:center;font-size:28px;font-weight:700;color:var(--brand)}
.title-rule{left:560px;width:80px;height:3px;background:var(--rule)}

/* services */
.services{top:660px;height:376px}
.service{width:150px;text-align:center;top:190px}
.service svg{display:block;margin:0 auto}
.service p{margin-top:20px;font-size:14px;color:var(--muted)}

/* welcome */
.welcome{top:1036px;height:485px;background:linear-gradient(90deg,#6e8fcc 0%,#4f7cc6 55%,#3c6dc2 100%)}
.welcome-photo{left:640px;top:0;width:560px;height:485px;background:linear-gradient(120deg,rgba(255,255,255,.0) 0%,rgba(150,180,230,.35) 60%,rgba(70,110,190,.2) 100%)}
.welcome h2{left:175px;top:82px;font-size:27px;font-weight:700;color:var(--white)}
.welcome .lead{left:175px;top:152px;width:520px;font-size:15px;font-weight:600;color:var(--white);line-height:25px}
.welcome .body{left:175px;top:217px;width:500px;font-size:14px;color:#eef2fb;line-height:24px}
.btn-outline-light{left:179px;top:355px;width:137px;height:46px;border:2px solid var(--white);color:var(--white);font-size:13px;font-weight:700;display:flex;align-items:center;justify-content:center}

/* blog */
.blog{top:1521px;height:623px}
.post{top:184px;width:285px}
.post-image{width:285px;height:114px}
.post h3{margin-top:86px;font-size:15px;font-weight:700;line-height:21px;color:var(--ink)}
.post p{margin-top:12px;font-size:12px;color:var(--muted);line-height:22px;width:260px}
.btn-outline{margin-top:18px;width:98px;height:32px;border:2px solid var(--brand);color:var(--brand);font-size:11px;font-weight:700;display:flex;align-items:center;justify-content:center}

/* video */
.video{top:2144px;height:471px;background:var(--soft)}
.video h2{left:132px;top:88px;font-size:28px;font-weight:700;color:var(--brand)}
.video h3{left:132px;top:150px;width:300px;font-size:16px;font-weight:700;line-height:23px;color:var(--ink)}
.video p{left:132px;top:212px;width:300px;font-size:13px;color:var(--muted);line-height:22px}
.video-btn{left:132px;top:314px;width:151px;height:47px}
.video-frame{left:453px;top:52px;width:615px;height:368px;background:linear-gradient(180deg,#5a4a56 0%,#b55a2c 30%,#f1a12e 60%,#e0771e 80%,#3a2418 100%)}
.play{left:305px;top:157px;width:80px;height:58px;background:#3b5c82;display:flex;align-items:center;justify-content:center}

/* newsletter */
.newsletter{top:2615px;height:325px;background:var(--brand)}
.newsletter h2{top:72px;color:var(--white)}
.newsletter .title-rule{top:117px;background:var(--white)}
.field{top:182px;height:56px;border:2px solid var(--white);color:var(--white);font-size:11px;padding-left:22px;display:flex;align-items:center}
.signup{left:783px;top:182px;width:128px;height:56px;background:var(--accent);color:var(--white);font-size:17px;font-weight:700;display:flex;align-items:center;justify-content:center}

/* footer */
.site-footer{top:2940px;height:424px;background:var(--white)}
.footer-brand{left:130px;top:66px;font-size:28px;font-weight:600;color:var(--brand);white-space:nowrap}
.follow{left:200px;top:162px;width:160px;text-align:center;font-size:12px;font-weight:700;color:var(--brand)}
.socials{left:228px;top:208px;display:flex;gap:10px}
.socials span{width:28px;height:28px;border-radius:50%;background:var(--brand)}
.socials span:nth-child(2){background:#1d8fe0}
.socials span:nth-child(3){background:#e0533d}
.footer-heading{font-size:12px;font-weight:700;color:var(--brand)}
.contact-item{left:567px;display:flex;align-items:flex-start;gap:18px;font-size:11px;color:var(--ink);line-height:23px}
.contact-icon{width:28px;height:28px;border-radius:50%;background:var(--brand);display:flex;align-items:center;justify-content:center;flex:none}
.menu{left:953px;top:108px;list-style:none;font-size:11px;color:var(--ink);line-height:28px}
.footer-rule{left:130px;top:328px;width:938px;height:1px;background:#d6d6d6}
.copyright{top:370px;left:0;width:1200px;text-align:center;font-size:10px;color:var(--ink)}
</style>
</head>
<body>

<header class="site-header">
  <div class="abs brand">Bright Summit Mentors</div>
  <div class="abs call">
    <span class="call-icon"><svg width="14" height="14" viewBox="0 0 24 24"><path fill="#fff" d="M6.6 10.8a15 15 0 0 0 6.6 6.6l2.2-2.2c.3-.3.7-.4 1-.2 1.1.4 2.3.6 3.6.6.6 0 1 .4 1 1V20c0 .6-.4 1-1 1A17 17 0 0 1 3 4c0-.6.4-1 1-1h3.5c.6 0 1 .4 1 1 0 1.2.2 2.4.6 3.6.1.3 0 .7-.2 1z"/></svg></span>
    <span class="call-label">CALL US :</span>
    <span class="call-number">(555) 014-2290</span>
  </div>
  <div class="abs search"><svg width="10" height="10" viewBox="0 0 24 24"><circle cx="10" cy="10" r="7" fill="none" stroke="#777" stroke-width="3"/><path d="M15 15l7 7" stroke="#777" stroke-width="3"/></svg>SEARCH</div>
</header>

<nav class="main-nav">
  <ul>
    <li class="active">HOME</li><li>ABOUT US</li><li>SERVICES</li><li>BLOG</li><li>TESTIMONIALS</li><li>CONTACT US</li>
  </ul>
</nav>

<section class="hero" role="img" aria-label="Woman in a sun hat with arms spread wide in a flower field under a blue sky">
  <h1 class="abs hero-title">Lifestyle Strategy</h1>
  <p class="abs hero-sub">Lorem Ipsum is simply dummy text</p>
  <div class="abs btn-solid hero-btn">READ MORE <svg width="8" height="10" viewBox="0 0 8 10"><path d="M1 0l6 5-6 5z" fill="#fff"/></svg></div>
  <div class="abs dots"><span></span><span></span><span></span><span></span><span></span></div>
</section>

<section class="services">
  <h2 class="abs section-title" style="top:52px">OUR SERVICES</h2>
  <div class="abs title-rule" style="top:113px"></div>

  <div class="abs service" style="left:149px">
    <svg width="70" height="70" viewBox="0 0 70 70" fill="var(--brand)"><circle cx="30" cy="12" r="7"/><path d="M20 22h20l8 14h14v6H44l-6-10-4 10H22z"/><rect x="8" y="44" width="56" height="6"/><rect x="12" y="50" width="5" height="14"/><rect x="55" y="50" width="5" height="14"/></svg>
    <p>Physical</p>
  </div>
  <div class="abs service" style="left:313px">
    <svg width="70" height="70" viewBox="0 0 70 70" fill="var(--brand)"><path d="M35 10c8 8 10 22 0 38-10-16-8-30 0-38z"/><path d="M10 24c12 2 20 12 22 26-14-2-22-12-22-26z"/><path d="M60 24c-12 2-20 12-22 26 14-2 22-12 22-26z"/><path d="M4 44c8 0 16 4 22 10H14c-6 0-10-4-10-10z"/><path d="M66 44c-8 0-16 4-22 10h12c6 0 10-4 10-10z"/></svg>
    <p>Spiritual</p>
  </div>
  <div class="abs service" style="left:495px">
    <svg width="70" height="70" viewBox="0 0 70 70"><rect x="8" y="14" width="54" height="44" rx="4" fill="var(--brand)"/><circle cx="35" cy="36" r="14" fill="#fff"/><text x="35" y="43" text-anchor="middle" font-family="Open Sans, sans-serif" font-size="20" font-weight="700" fill="var(--brand)">$</text><rect x="2" y="24" width="8" height="24" fill="var(--brand)"/><rect x="60" y="24" width="8" height="24" fill="var(--brand)"/></svg>
    <p>Financial</p>
  </div>
  <div class="abs service" style="left:679px">
    <svg width="70" height="70" viewBox="0 0 70 70" fill="var(--brand)"><circle cx="35" cy="12" r="7"/><rect x="27" y="22" width="16" height="28" rx="4"/><circle cx="17" cy="18" r="6"/><rect x="10" y="27" width="14" height="26" rx="4"/><circle cx="53" cy="18" r="6"/><rect x="46" y="27" width="14" height="26" rx="4"/><rect x="30" y="48" width="4" height="16"/><rect x="36" y="48" width="4" height="16"/></svg>
    <p>Leadership</p>
  </div>
  <div class="abs service" style="left:885px">
    <svg width="70" height="70" viewBox="0 0 70 70" fill="var(--brand)"><circle cx="35" cy="12" r="7"/><path d="M25 30a10 10 0 0 1 20 0z"/><path d="M34 30v8H16v8h3v-5h14v-3h4v3h14v5h3v-8H36v-8z"/><circle cx="17" cy="50" r="6"/><path d="M7 66a10 10 0 0 1 20 0z"/><circle cx="53" cy="50" r="6"/><path d="M43 66a10 10 0 0 1 20 0z"/></svg>
    <p>Relationship Goals</p>
  </div>
</section>

<section class="welcome">
  <div class="abs welcome-photo" role="img" aria-label="Joyful woman leaping with arms outstretched"></div>
  <h2 class="abs">WELCOME TO OUR SITE</h2>
  <p class="abs lead">There are many variations of passages of Lorem Ipsum available, but the majority have suffered alteration</p>
  <p class="abs body">It is a long established fact that a reader will be distracted by the readable content of a page when looking at its layout. The point of using Lorem Ipsum is that it has a more-or-less normal distribution of letters, as opposed to using</p>
  <div class="abs btn-outline-light">READ MORE</div>
</section>

<section class="blog">
  <h2 class="abs section-title" style="top:52px">LATEST BLOG</h2>
  <div class="abs title-rule" style="top:117px"></div>

  <article class="abs post" style="left:132px">
    <div class="post-image" role="img" aria-label="Person with raised arms in a golden field at sunrise" style="background:linear-gradient(180deg,#b98c4a 0%,#f2c25a 45%,#8a6a2e 75%,#3e2e14 100%)"></div>
    <h3>THERE ARE MANY VARIATIONS OF PASSAGES OF LOREM</h3>
    <p>Contrary to popular belief, Lorem Ipsum is not simply random text. It has roots.</p>
    <div class="btn-outline">READ MORE</div>
  </article>
  <article class="abs post" style="left:453px">
    <div class="post-image" role="img" aria-label="Person meditating on a rock by the sea" style="background:linear-gradient(180deg,#1f6fa8 0%,#6fc0de 45%,#bfe4ee 60%,#2a5d74 100%)"></div>
    <h3>IT IS A LONG ESTABLISHED FACT THAT A READER WILL</h3>
    <p>Contrary to popular belief, Lorem Ipsum is not simply random text. It has roots.</p>
    <div class="btn-outline">READ MORE</div>
  </article>
  <article class="abs post" style="left:783px">
    <div class="post-image" role="img" aria-label="Woman with arms raised in a wheat field" style="background:linear-gradient(180deg,#f1d98a 0%,#f6e6ad 40%,#d8a53a 70%,#a77620 100%)"></div>
    <h3>CONTRARY TO POPULAR BELIEF, LOREM IPSUM IS</h3>
    <p>Contrary to popular belief, Lorem Ipsum is not simply random text. It has roots.</p>
    <div class="btn-outline">READ MORE</div>
  </article>
</section>

<section class="video">
  <h2 class="abs">OUR VIDEO</h2>
  <h3 class="abs">IT IS A LONG ESTABLISHED FACT THAT A READER WILL</h3>
  <p class="abs">There are many variations of passages of Lorem Ipsum available, but the majority have suffered alteration .</p>
  <div class="abs btn-solid video-btn">WATCH VIDEO</div>
  <div class="abs video-frame" role="img" aria-label="Silhouette of a woman jumping against an orange sunset">
    <div class="abs play"><svg width="22" height="26" viewBox="0 0 22 26"><path d="M0 0l22 13L0 26z" fill="#fff"/></svg></div>
  </div>
</section>

<section class="newsletter">
  <h2 class="abs section-title">NEWSLETTER SIGNUP</h2>
  <div class="abs title-rule"></div>
  <div class="abs field" style="left:278px;width:233px">NAME</div>
  <div class="abs field" style="left:532px;width:233px">E MAIL ID</div>
  <div class="abs signup">SIGNUP</div>
</section>

<footer class="site-footer">
  <div class="abs footer-brand">Bright Summit Mentors</div>
  <div class="abs follow">FOLLOW US</div>
  <div class="abs socials"><span></span><span></span><span></span></div>

  <div class="abs footer-heading" style="left:567px;top:70px">CONTACT US</div>
  <div class="abs contact-item" style="top:134px">
    <span class="contact-icon"><svg width="12" height="14" viewBox="0 0 24 28"><path fill="#fff" d="M12 0a10 10 0 0 0-10 10c0 8 10 18 10 18s10-10 10-18A10 10 0 0 0 12 0zm0 14a4 4 0 1 1 0-8 4 4 0 0 1 0 8z"/></svg></span>
    <span>42 Ridgeview Road<br>Alder Falls, OR 97001</span>
  </div>
  <div class="abs contact-item" style="top:195px">
    <span class="contact-icon"><svg width="12" height="12" viewBox="0 0 24 24"><path fill="#fff" d="M6.6 10.8a15 15 0 0 0 6.6 6.6l2.2-2.2c.3-.3.7-.4 1-.2 1.1.4 2.3.6 3.6.6.6 0 1 .4 1 1V20c0 .6-.4 1-1 1A17 17 0 0 1 3 4c0-.6.4-1 1-1h3.5c.6 0 1 .4 1 1 0 1.2.2 2.4.6 3.6.1.3 0 .7-.2 1z"/></svg></span>
    <span>555.014.2290</span>
  </div>
  <div class="abs contact-item" style="top:242px">
    <span class="contact-icon"><svg width="12" height="10" viewBox="0 0 24 18"><rect width="24" height="18" rx="2" fill="#fff"/><path d="M1 2l11 8 11-8" fill="none" stroke="var(--brand)" stroke-width="2"/></svg></span>
    <span>hello@brightsummitmentors.com</span>
  </div>

  <div class="abs footer-heading" style="left:953px;top:70px">MENU</div>
  <ul class="abs menu">
    <li>Home</li><li>About us</li><li>Services</li><li>Blog</li><li>Testimonials</li><li>Contact us</li>
  </ul>

  <div class="abs footer-rule"></div>
  <p class="abs copyright">Copyrights © 2017 All Rights Reserved</p>
</footer>

</body>
</html>
```